Veldmark Supplies Business Card

Professional business card that stand out to our potential customers. Front and back with clean modern design

Industry/Entity Type

Oil and gas

Contact Information for Business Card

Name, address, website , office phone and cell number

Requirements
Must have
• Editable files for each employee

```html
<!DOCTYPE html>
<html lang="en">
<head>
<meta charset="utf-8">
<title>Veldmark Supplies Business Card</title>
<link rel="stylesheet" href="https://fonts.googleapis.com/css2?family=Roboto:wght@400;500;700&display=swap">
<style>
  :root {
    --bg: #2b2b2d;
    --card: #1d1e20;
    --red: #e2232a;
    --blue: #27b3d6;
    --white: #ffffff;
  }
  * { box-sizing: border-box; margin: 0; padding: 0; }
  html, body { width: 1200px; height: 852px; overflow: hidden; }
  body {
    background: var(--bg);
    font-family: "Roboto", Arial, sans-serif;
    position: relative;
  }
  .card {
    position: absolute;
    width: 520px;
    height: 297px;
    background: var(--card);
    border-radius: 18px;
    overflow: hidden;
  }
  .card--front { left: 50px; top: 278px; }
  .card--back { left: 630px; top: 278px; }

  .front-brand {
    position: absolute;
    inset: 0;
    display: flex;
    align-items: center;
    justify-content: center;
    gap: 14px;
  }
  .brand-square {
    width: 22px; height: 22px;
    background: var(--red);
    flex: none;
  }
  .brand-name {
    font-weight: 700;
    text-transform: uppercase;
    letter-spacing: 1px;
    color: var(--blue);
    white-space: nowrap;
  }
  .front-brand .brand-name { font-size: 28px; }

  .back-art { position: absolute; inset: 0; width: 520px; height: 297px; }

  .back-brand {
    position: absolute;
    right: 28px; top: 26px;
    display: flex; align-items: center; gap: 10px;
  }
  .back-brand .brand-name { font-size: 22px; }

  .person {
    position: absolute;
    left: 34px; top: 150px;
  }
  .person__name {
    font-size: 19px; font-weight: 700; color: var(--blue);
  }
  .person__title {
    font-size: 11px; color: var(--white); margin-top: 2px;
  }

  .contact {
    position: absolute;
    right: 22px; top: 110px;
    list-style: none;
    color: var(--white);
    font-size: 11px;
    line-height: 19px;
  }
  .contact li {
    display: flex; justify-content: flex-end; align-items: center; gap: 7px;
    white-space: nowrap;
  }
  .contact svg { width: 11px; height: 11px; fill: var(--white); flex: none; }
  .contact .no-icon { padding-right: 18px; }
</style>
</head>
<body>

<section class="card card--front" aria-label="Card front">
  <div class="front-brand">
    <span class="brand-square"></span>
    <span class="brand-name">Veldmark Supplies</span>
  </div>
</section>

<section class="card card--back" aria-label="Card back">
  <svg class="back-art" viewBox="0 0 520 297" aria-hidden="true">
    <path d="M0,262 C140,262 190,235 230,175 C270,112 350,96 520,90 L520,297 L0,297 Z" fill="var(--red)"/>
    <path d="M-4,247 C136,247 180,222 218,163 C258,100 345,82 524,76" fill="none" stroke="var(--blue)" stroke-width="7"/>
  </svg>

  <div class="back-brand">
    <span class="brand-square"></span>
    <span class="brand-name">Veldmark Supplies</span>
  </div>

  <div class="person">
    <p class="person__name">Daniel Reyes Hart</p>
    <p class="person__title">Managing Director</p>
  </div>

  <ul class="contact">
    <li>(555)014-2290
      <svg viewBox="0 0 24 24"><path d="M6.6 10.8a15 15 0 0 0 6.6 6.6l2.2-2.2c.3-.3.7-.4 1-.2 1.1.4 2.3.6 3.6.6.6 0 1 .4 1 1V20c0 .6-.4 1-1 1A17 17 0 0 1 3 4c0-.6.4-1 1-1h3.5c.6 0 1 .4 1 1 0 1.3.2 2.5.6 3.6.1.3 0 .7-.2 1z"/></svg>
    </li>
    <li>www.veldmarksupplies.com
      <svg viewBox="0 0 24 24"><circle cx="12" cy="12" r="10"/></svg>
    </li>
    <li>sales@veldmarksupplies.com
      <svg viewBox="0 0 24 24"><path d="M2 5h20v14H2z M4 7v.5l8 5 8-5V7l-8 5z" fill-rule="evenodd"/></svg>
    </li>
    <li class="no-icon">418 Corwin Rd Suite 2 Kestrel, Tx 79012</li>
  </ul>
</section>

</body>
</html>
```